Design a Website for an IT Support Company

We are an IT support company that provides commercial IT support and services to small and medium sized businesses. We are in need of a website to be developed for our business.
We would like to work with someone who is either familiar with the IT field, or has developed a website for an IT support company in the past.
Some examples of designs/layouts that we like:
https://www.veldaworks.example/
http://www.marsbyquill.example/
http://817kq.example/
http://www.olbenstructures.example/
http://www.bykq.example/
I have attached a word document that gives a menu system/page layout format that we would like for our website as well as branch office phone numbers. Our logo is also attached that you can use for your design purposes. We currently do not have copy produced for all of the pages outlined in the word document, but would get this done during the project with the selected designer.
We would like the website to be SEO friendly & fully responsive. We would prefer a Wordpress format, however, we are open to HTML formats as well.

```html
<!DOCTYPE html>
<html lang="en">
<head>
<meta charset="utf-8">
<title>Vantaro IT — Commercial IT Support</title>
<link rel="stylesheet" href="https://fonts.googleapis.com/css2?family=Exo+2:wght@600;700&family=Poppins:wght@400;500&family=Arimo:wght@400;700&family=Open+Sans:wght@400;600&display=swap">
<style>
:root{
  --blue:#1a6fb5;
  --blue-deep:#0f64ad;
  --footer:#2f74b8;
  --footer-dark:#1f5d99;
  --bar:#3d3d3d;
  --ink:#555;
  --muted:#6a6a6a;
  --light:#f4f6f8;
  --hero-text:#8fd0ff;
  --white:#fff;
  --star:#e2b400;
}
*{margin:0;padding:0;box-sizing:border-box}
html,body{width:673px;height:1200px;overflow:hidden;background:var(--white)}
body{position:relative;font-family:"Arimo",Arial,sans-serif;color:var(--ink)}

/* header */
.site-header{position:absolute;left:0;top:0;width:673px;height:61px;background:var(--white);border-top:2px solid var(--blue)}
.contact-tab{position:absolute;left:360px;top:0;width:268px;height:22px;background:var(--blue);clip-path:polygon(0 0,100% 0,96% 100%,4% 100%);color:var(--white);font:400 7.5px "Poppins",sans-serif;display:flex;align-items:center;justify-content:center;gap:16px;white-space:nowrap}
.contact-tab span{display:flex;align-items:center;gap:5px}
.contact-tab svg{flex:none}
.brand{position:absolute;left:48px;top:24px;display:flex;align-items:center;gap:6px;font:700 17px "Exo 2",sans-serif;color:var(--blue-deep)}
.brand .dot{width:14px;height:14px;border-radius:50%;background:var(--blue)}
.main-nav{position:absolute;top:40px;left:317px;font:600 6.5px "Open Sans",sans-serif;color:#444;letter-spacing:.2px}
.main-nav a{position:absolute;text-decoration:none;color:inherit;white-space:nowrap}
.main-nav .nav-home{color:var(--blue)}
.nav-home::after{content:"";position:absolute;left:-6px;right:-6px;top:21px;height:2px;background:var(--blue)}
.search-btn{position:absolute;left:603px;top:34px;width:21px;height:21px;border-radius:50%;background:var(--blue)}

/* hero */
.hero{position:absolute;left:0;top:61px;width:673px;height:305px;overflow:hidden}
.hero-photo{position:absolute;inset:0;background:radial-gradient(circle at 72% 62%,#e8a24c 0,#6b4a2a 10%,transparent 28%),radial-gradient(ellipse at 62% 40%,#1f6f86 0,#0c2e3c 35%,#050a0e 70%),#05080b}
.hero-title{position:absolute;left:49px;top:94px;font:700 26px "Exo 2",sans-serif;color:var(--white);letter-spacing:.5px}
.hero-sub{position:absolute;left:49px;top:129px;font:400 11.5px "Poppins",sans-serif;color:var(--hero-text)}
.hero-copy{position:absolute;left:49px;top:155px;width:270px;font-size:6.5px;line-height:14.5px;color:var(--white)}
.btn-outline{position:absolute;left:49px;top:213px;width:97px;height:30px;border:1px solid var(--hero-text);border-radius:15px;font:500 9.5px "Poppins",sans-serif;color:var(--hero-text);display:flex;align-items:center;justify-content:center;letter-spacing:.4px}
.slider-dots{position:absolute;left:49px;top:281px;display:flex;gap:1px}
.slider-dots i{width:8px;height:8px;border:1px solid var(--white);border-radius:50%}
.slider-dots i.on{border-color:var(--blue)}

/* section headings */
.section-title{position:absolute;left:0;width:673px;text-align:center;font:700 13px "Exo 2",sans-serif;color:var(--blue);letter-spacing:.5px}
.section-lead{position:absolute;left:0;width:673px;text-align:center;font-size:6.5px;color:var(--muted)}

/* services */
.service{position:absolute;top:446px;width:180px;text-align:center}
.service-icon{width:64px;height:64px;margin:0 auto;border-radius:50%;background:var(--blue-deep);display:flex;align-items:center;justify-content:center}
.service h3{margin-top:8px;font:700 10px "Exo 2",sans-serif;color:var(--blue);letter-spacing:.4px}
.service p{width:152px;margin:5px auto 0;font-size:6.5px;line-height:14.5px;color:var(--muted)}

/* why */
.why{position:absolute;left:0;top:600px;width:673px;height:219px;background:var(--light)}
.why-photo{position:absolute;left:362px;top:0;width:311px;height:219px;background:linear-gradient(100deg,#e9eef2 0,#cfd9e2 35%,#9fb3c6 60%,#dfe6ec 100%)}
.why h2{position:absolute;left:49px;top:22px;font:700 13px "Exo 2",sans-serif;color:var(--blue);letter-spacing:.4px}
.why p{position:absolute;left:49px;width:285px;font-size:6.5px;line-height:14.5px;color:var(--muted)}
.btn-solid{position:absolute;left:49px;top:177px;width:72px;height:24px;background:var(--blue-deep);color:var(--white);font:700 8px "Exo 2",sans-serif;display:flex;align-items:center;justify-content:center;letter-spacing:.3px}

/* testimonials */
.testimonial{position:absolute;top:905px;width:200px;height:100px}
.avatar{position:absolute;left:0;top:0;width:48px;height:48px;border-radius:50%;border:2px solid #ddd;background:linear-gradient(160deg,#caa58a,#6c5446)}
.quote{position:absolute;left:61px;top:3px;width:125px;font-size:6.5px;line-height:12px;color:var(--muted)}
.quote b{font:700 10px Georgia,serif;color:#999;margin-right:3px}
.t-name{position:absolute;left:61px;top:63px;font:700 6.5px "Arimo",sans-serif;color:var(--blue)}
.t-date{position:absolute;left:61px;top:75px;font-size:6px;color:#555}
.t-stars{position:absolute;left:61px;top:85px;font-size:7px;color:var(--star);letter-spacing:.5px}

/* footer */
.site-footer{position:absolute;left:0;top:1026px;width:673px;height:137px;background:var(--footer);color:var(--white)}
.footer-brand{position:absolute;left:48px;top:52px;display:flex;align-items:center;gap:7px;font:700 21px "Exo 2",sans-serif;color:var(--white)}
.footer-brand .dot{width:18px;height:18px;border-radius:50%;border:2px solid var(--white)}
.footer-col-title{position:absolute;font:700 9.5px "Arimo",sans-serif;letter-spacing:.2px}
.branches{position:absolute;left:221px;top:51px;font-size:6.5px;line-height:13px;border-collapse:collapse}
.branches td{padding:0}
.branches td:nth-child(2){width:14px;text-align:center}
.news-copy{position:absolute;left:359px;top:51px;width:120px;font-size:6.5px;line-height:11.5px}
.email-field{position:absolute;left:359px;top:82px;width:133px;height:18px;background:var(--white);color:#888;font-size:6.5px;padding-left:8px;display:flex;align-items:center}
.subscribe{position:absolute;left:359px;top:105px;width:45px;height:15px;background:var(--footer-dark);font-size:6px;display:flex;align-items:center;justify-content:center}
.follow-copy{position:absolute;left:508px;top:53px;width:125px;font-size:6px;line-height:10.5px}
.social{position:absolute;left:507px;top:95px;display:flex;gap:4px}
.social i{width:20px;height:20px;border:1.5px solid var(--white);border-radius:50%}
.copyright-bar{position:absolute;left:0;top:1163px;width:673px;height:37px;background:var(--bar);color:var(--white);font:400 6.5px "Open Sans",sans-serif;display:flex;align-items:center;justify-content:center}
</style>
</head>
<body>

<header class="site-header">
  <div class="contact-tab">
    <span><svg width="8" height="8" viewBox="0 0 24 24"><path fill="#fff" d="M6.6 10.8a15 15 0 0 0 6.6 6.6l2.2-2.2c.3-.3.7-.4 1-.2 1.1.4 2.3.6 3.6.6.6 0 1 .4 1 1V20c0 .6-.4 1-1 1A17 17 0 0 1 3 4c0-.6.4-1 1-1h3.5c.6 0 1 .4 1 1 0 1.3.2 2.5.6 3.6.1.3 0 .7-.2 1z"/></svg>Call Us : 555-014-2200</span>
    <span><svg width="9" height="8" viewBox="0 0 24 20"><rect x="1" y="1" width="22" height="18" rx="2" fill="none" stroke="#fff" stroke-width="2"/><path d="M1 3l11 8 11-8" fill="none" stroke="#fff" stroke-width="2"/></svg>Email :info@vantaro.example</span>
  </div>
  <div class="brand"><span class="dot"></span>Vantaro IT</div>
  <nav class="main-nav">
    <a class="nav-home" href="#" style="left:0">HOME</a>
    <a href="#" style="left:61px">ABOUT US</a>
    <a href="#" style="left:135px">WHY VANTARO IT</a>
    <a href="#" style="left:234px">CONTACT US</a>
  </nav>
  <div class="search-btn"><svg width="21" height="21" viewBox="0 0 21 21"><circle cx="10" cy="10" r="2.6" fill="none" stroke="#fff" stroke-width="1.3"/><path d="M12 12l2 2" stroke="#fff" stroke-width="1.3"/></svg></div>
</header>

<section class="hero">
  <div class="hero-photo" role="img" aria-label="Hand holding a glowing wireless signal symbol against a dark teal background"></div>
  <h1 class="hero-title">VANTARO IT</h1>
  <p class="hero-sub">That Provides Commercial IT Support &amp; Services</p>
  <p class="hero-copy">Sed ut perspiciatis unde omnis iste natus error sit voluptatem accusantium doloremque laudantium, totam rem aperiam, eaque ipsa quae ab illo inventore veritatis et quasi architecto beatae vitae dicta sunt explicabo.</p>
  <a class="btn-outline">READ MORE</a>
  <div class="slider-dots"><i></i><i></i><i class="on"></i><i></i><i></i></div>
</section>

<h2 class="section-title" style="top:385px">OUR SERVICES</h2>
<p class="section-lead" style="top:410px">Sed ut perspiciatis unde omnis iste natus error sit voluptatem accusantium doloremque laudantium, totam rem aperiam, eaque ipsa quae</p>

<div class="service" style="left:52px">
  <div class="service-icon"><svg width="30" height="30" viewBox="0 0 30 30"><ellipse cx="13" cy="6" rx="9" ry="3.5" fill="#fff"/><path d="M4 9c0 2 4 3.5 9 3.5s9-1.5 9-3.5v4c0 2-4 3.5-9 3.5S4 15 4 13z" fill="#fff"/><path d="M4 16c0 2 4 3.5 9 3.5v4C8 23.5 4 22 4 20z" fill="#fff"/><circle cx="22" cy="22" r="4" fill="none" stroke="#fff" stroke-width="2.5" stroke-dasharray="2 1.2"/></svg></div>
  <h3>DATA</h3>
  <p>Sed ut perspiciatis unde omnis iste natus error sit voluptatem accusantium doloremque laudantium, beatae vitae dicta sunt explicabo.</p>
</div>
<div class="service" style="left:247px">
  <div class="service-icon"><svg width="32" height="30" viewBox="0 0 32 30"><path d="M9 20H8a6 6 0 0 1 0-12 8 8 0 0 1 15-1 6.5 6.5 0 0 1 1 13h-1" fill="none" stroke="#fff" stroke-width="2"/><path d="M16 12v14M12 22l4 4 4-4" fill="none" stroke="#fff" stroke-width="2"/></svg></div>
  <h3>CLOUD</h3>
  <p>Sed ut perspiciatis unde omnis iste natus error sit voluptatem accusantium doloremque laudantium, beatae vitae dicta sunt explicabo.</p>
</div>
<div class="service" style="left:442px">
  <div class="service-icon"><svg width="26" height="30" viewBox="0 0 26 30"><rect x="8" y="2" width="10" height="17" rx="5" fill="#fff"/><path d="M4 14a9 9 0 0 0 18 0M13 23v5M8 28h10" fill="none" stroke="#fff" stroke-width="2"/></svg></div>
  <h3>VOICE</h3>
  <p>Sed ut perspiciatis unde omnis iste natus error sit voluptatem accusantium doloremque laudantium, beatae vitae dicta sunt explicabo.</p>
</div>

<section class="why">
  <div class="why-photo" role="img" aria-label="Support team wearing headsets at computers in a bright office"></div>
  <h2>WHY VANTARO IT</h2>
  <p style="top:49px">Sed ut perspiciatis unde omnis iste natus error sit voluptatem accusantium doloremque laudan-tium, totam rem aperiam, eaque ipsa quae ab illo inventore veritatis et quasi architecto beatae vitae dicta sunt explicabo. Nemo enim ipsam voluptatem quia voluptas sit aspernatur aut odit aut  magni dolores eos qui ratione voluptatem sequi nesciunt.</p>
  <p style="top:120px">Sed ut perspiciatis unde omnis iste natus error sit voluptatem accusantium doloremque laudan-tium, totam rem aperiam, eaque ipsa quae ab illo inventore veritatis et quasi architecto beatae magni dolores eos qui ratione voluptatem sequi nesciunt.</p>
  <a class="btn-solid">READ MORE</a>
</section>

<h2 class="section-title" style="top:845px">OUR TESTIMONIALS</h2>
<p class="section-lead" style="top:870px">Sed ut perspiciatis unde omnis iste natus error sit voluptatem accusantium doloremque laudantium, totam rem aperiam, eaque ipsa quae</p>

<div class="testimonial" style="left:49px">
  <div class="avatar" role="img" aria-label="Customer portrait"></div>
  <p class="quote"><b>“</b>Sed ut perspiciatis unde omnis iste natus error sit voluptatem accusantium doloremque laudantium, totam rem vitae dicta sunt explicabo.</p>
  <div class="t-name">DANA ROWE</div><div class="t-date">POSTED ON 25 JULY 2017</div><div class="t-stars">☆☆☆☆ ★</div>
</div>
<div class="testimonial" style="left:246px">
  <div class="avatar" role="img" aria-label="Customer portrait"></div>
  <p class="quote"><b>“</b>Sed ut perspiciatis unde omnis iste natus error sit voluptatem accusantium doloremque laudantium, totam rem vitae dicta sunt explicabo.</p>
  <div class="t-name">DANA ROWE</div><div class="t-date">POSTED ON 25 JULY 2017</div><div class="t-stars">☆☆☆☆ ★</div>
</div>
<div class="testimonial" style="left:442px">
  <div class="avatar" role="img" aria-label="Customer portrait"></div>
  <p class="quote"><b>“</b>Sed ut perspiciatis unde omnis iste natus error sit voluptatem accusantium doloremque laudantium, totam rem vitae dicta sunt explicabo.</p>
  <div class="t-name">DANA ROWE</div><div class="t-date">POSTED ON 25 JULY 2017</div><div class="t-stars">☆☆☆☆ ★</div>
</div>

<footer class="site-footer">
  <div class="footer-brand"><span class="dot"></span>Vantaro IT</div>
  <h4 class="footer-col-title" style="left:220px;top:27px">CONTACT US</h4>
  <table class="branches">
    <tr><td>Main Number</td><td>:</td><td>555-014-2200</td></tr>
    <tr><td>Houston</td><td>:</td><td>555-016-3100</td></tr>
    <tr><td>San Antonio</td><td>:</td><td>555-018-4400</td></tr>
    <tr><td>Austin</td><td>:</td><td>555-019-5500</td></tr>
    <tr><td>Tulsa</td><td>:</td><td>555-012-6600</td></tr>
    <tr><td>Oklahoma City</td><td>:</td><td>555-017-7700</td></tr>
  </table>
  <h4 class="footer-col-title" style="left:358px;top:27px">NEWSLETTER</h4>
  <p class="news-copy">Register Your email address to get information ablout us</p>
  <div class="email-field">Email Address</div>
  <div class="subscribe">SUBSCRIBE</div>
  <h4 class="footer-col-title" style="left:508px;top:28px">FOLLOW US</h4>
  <p class="follow-copy">Lorem ipsum dolor sit amet, conse ctetur adipiscing elit. Nulla in purus nibh. Donec ornare</p>
  <div class="social"><i></i><i></i><i></i><i></i><i></i></div>
</footer>
<div class="copyright-bar">© Copyright 2017 Vantaro .All Rights Reserved</div>

</body>
</html>
```